Specialised investor in e-mobility and energy wants business card design

We need a business card design that fits our existing corporate design. <The look and feel must be 'sharp'/'clean', dynamic, communicate momentum, professionalism etc (as one would imagine from a firm in the financial sector). We like the idea of a reverse-side of the card that includes the logo, and the name and contact details on the other. We expect the deliverable to be whatever format might be required to be able to get cards printed directly by a service such as kelmo press. Our website is www.zub.capital

```html
<!DOCTYPE html>
<html lang="en">
<head>
<meta charset="utf-8">
<title>Zub Capital – Business Card</title>
<link href="https://fonts.googleapis.com/css2?family=Montserrat:wght@400;500;700&display=swap" rel="stylesheet">
<style>
  :root {
    --bg: #e6e6e3;
    --card: #ffffff;
    --green-dark: #2f4f23;
    --green-light: #86b04a;
    --ink: #333333;
  }
  html, body { margin: 0; padding: 0; overflow: hidden; }
  body {
    width: 1200px; height: 801px;
    background: var(--bg);
    font-family: 'Montserrat', Arial, sans-serif;
    position: relative;
  }
  .card {
    position: absolute;
    top: 232px;
    width: 520px; height: 336px;
    background: var(--card);
    box-shadow: 0 6px 18px rgba(0,0,0,0.12);
    overflow: hidden;
  }
  .card--front { left: 60px; }
  .card--back { left: 620px; }
  .swoosh { position: absolute; inset: 0; }
  .wordmark {
    position: absolute;
    display: flex; align-items: center; gap: 8px;
    color: var(--green-dark);
    font-weight: 500;
    letter-spacing: 0.5px;
    white-space: nowrap;
  }
  .wordmark__dot { background: var(--green-light); display: block; }
  .card--front .wordmark { left: 36px; top: 150px; font-size: 30px; }
  .card--front .wordmark__dot { width: 10px; height: 10px; }
  .divider {
    position: absolute; left: 272px; top: 70px;
    width: 1px; height: 130px;
    background: var(--green-light);
  }
  .details {
    position: absolute; left: 290px; top: 34px;
    color: var(--ink); font-size: 11px; line-height: 16px;
  }
  .details__name {
    color: var(--green-light); font-weight: 700; font-size: 15px;
    letter-spacing: 0.5px; margin: 0; line-height: 18px;
  }
  .details__role { margin: 0 0 10px; font-size: 11.5px; }
  .contact { list-style: none; margin: 0 0 8px; padding: 0; }
  .contact li { display: flex; align-items: center; gap: 6px; }
  .contact svg { width: 9px; height: 9px; fill: var(--green-light); flex: none; }
  .details__company { color: var(--green-light); margin: 0; }
  .details__city { margin: 0; }
  .card--back .wordmark {
    left: 0; right: 0; top: 0; bottom: 0; justify-content: center;
    font-size: 58px;
  }
  .card--back .wordmark__dot { width: 16px; height: 16px; }
</style>
</head>
<body>
  <section class="card card--front" aria-label="Business card front">
    <svg class="swoosh" viewBox="0 0 520 336" aria-hidden="true">
      <path d="M226 336 C 284 244, 392 184, 520 144 L520 160 C 396 198, 298 256, 244 336 Z" fill="var(--green-light)"/>
      <path d="M252 336 C 304 262, 404 206, 520 176 L520 336 Z" fill="var(--green-dark)"/>
    </svg>
    <div class="wordmark"><span class="wordmark__dot"></span>zub capital</div>
    <div class="divider"></div>
    <div class="details">
      <p class="details__name">ELIAS BRANDT</p>
      <p class="details__role">Managing Director</p>
      <ul class="contact">
        <li><svg viewBox="0 0 10 10"><path d="M2 0.5 L4 2.5 L3 4 Q4.5 6 6 7 L7.5 6 L9.5 8 L8 9.5 Q3 9 0.5 2 Z"/></svg>+41 70 555 0142</li>
        <li><svg viewBox="0 0 10 10"><path d="M0 2 H10 V8 H0 Z M0 2 L5 5.5 L10 2" /></svg>elias@zub.capital</li>
        <li><svg viewBox="0 0 10 10"><circle cx="5" cy="5" r="5"/></svg>www.zub.capital</li>
      </ul>
      <p class="details__company">Zub Capital S.A.</p>
      <p class="details__city">Lugano, Switzerland</p>
    </div>
  </section>

  <section class="card card--back" aria-label="Business card back">
    <div class="wordmark"><span class="wordmark__dot"></span>zub capital</div>
  </section>
</body>
</html>
```